Advanced Therapeutic Massage Therapist

I need a business card advertising my massage services as an advanced therapeutic massage therapist. I offer advanced therapeutic massage, swedish and deep tissue. I want to create a simple, professional and feminine card. I like bright colours and creativity.

I prefer a bold and experimental approach rather than something status-quo. A card to suggest therapeutic healing through dynamic massage. Motifs, shapes or layout which suggest movement and flow.
Updates

Target Market(s)

Everybody!

Industry/Entity Type

Health And Wellness

Contact Information for Business Card

The card should include:
My name, logo, services offered and my contact details.

Sláine Dunleavy
Massage Therapist

- Swedish - Deep Tissue - Advanced Therapeutic

Phone: (+353) 87 216 4093
Email: regenerate@slainedunleavy-example.com
Website: www.slainedunlevy-example.com

Font styles to use
Serif
Sans Serif
Decorative
Script

Colors

Designer to choose colors to be used in the design.

Requirements
Must have
• An example may contain something like this, yet concise:
• "Sláine Dunleavy
• Massage Therapist
• - Swedish - Deep Tissue - Advanced Therapeutic"
Nice to have
• This sentence is optional:
• Imagery such as a logo or symbol. I have attached a file containing a logo I had produced however the name is incorrect now as it is "Sláine" not "Nelly". It could be edited to change it to Sláine.
• I have sent the file as .psd .jpg. .pdf and .png
• I like when the card conveys energy, movement, pressure points, flow etc.
• I just like the designer to follow their own style and ideas. I like bright colours but must have a lot of a base colour to offset it. I really prefer them to follow their own inspiration. That is my preference.
Should not have
• Pine trees, non-native trees to Britain and Ireland, exotic flowers or animals that are not native to Britain and Ireland.
• I don't like brown as the background colour of the card.
• The cars shouldn't look like a wedding invitation i.e too many floral type designs.

```html
<!DOCTYPE html>
<html lang="en">
<head>
<meta charset="utf-8">
<title>Sláine Dunleavy – Massage Therapist Business Card</title>
<link rel="stylesheet" href="https://fonts.googleapis.com/css2?family=Open+Sans:wght@400;600;700&family=Great+Vibes&family=Quicksand:wght@400;500&display=swap">
<style>
  :root {
    --stage: #000000;
    --card-light: #f3f3f3;
    --card-teal: #1f5f5c;
    --ink: #141414;
    --name-sage: #7f8466;
    --mint: #bfe6d9;
    --mint-deep: #9fd3c3;
    --gold: #c9a14a;
    --cream: #f1e9dd;
    --dot: #8f8a7a;
  }
  * { margin: 0; padding: 0; box-sizing: border-box; }
  html, body { width: 1200px; height: 900px; overflow: hidden; background: var(--stage); }
  .canvas { position: relative; width: 1200px; height: 900px; }

  .card { position: absolute; top: 200px; width: 310px; height: 502px; }
  .card--front { left: 265px; background: var(--card-light); border-radius: 62px 0 62px 0; font-family: "Open Sans", Arial, sans-serif; color: var(--ink); }
  .card--back { left: 641px; width: 309px; background: var(--card-teal); border-radius: 0 62px 0 62px; }

  .logo-mark { position: absolute; display: flex; align-items: center; justify-content: center; border-radius: 50%; background: radial-gradient(circle, var(--mint) 0%, var(--mint-deep) 100%); border: 3px solid var(--gold); }
  .logo-mark--small { left: 142px; top: 41px; width: 144px; height: 144px; }
  .logo-mark--large { left: 64px; top: 133px; width: 180px; height: 180px; box-shadow: 0 0 0 8px rgba(201,161,74,0.25); }
  .logo-mark__name { font-family: "Open Sans", Arial, sans-serif; font-weight: 600; font-size: 14px; color: #6f5a2a; text-align: center; line-height: 1.3; }

  .holder { position: absolute; left: 24px; top: 312px; }
  .holder__name { font-size: 18px; font-weight: 700; color: var(--name-sage); line-height: 1.2; }
  .holder__role { font-size: 13.5px; margin-top: 2px; }

  .contact { position: absolute; left: 24px; top: 372px; list-style: none; font-size: 12.5px; }
  .contact li { display: flex; align-items: center; gap: 7px; height: 20px; white-space: nowrap; }
  .contact svg { width: 10px; height: 10px; flex: none; }

  .services { position: absolute; left: 24px; top: 440px; list-style: none; font-size: 13.5px; font-weight: 700; display: flex; flex-wrap: wrap; width: 230px; row-gap: 3px; }
  .services li { display: flex; align-items: center; height: 18px; }
  .services li::before { content: ""; width: 8px; height: 8px; border-radius: 50%; background: radial-gradient(circle at 35% 35%, #d6d2c6, var(--dot)); margin-right: 6px; }
  .services li:nth-child(2)::before { margin-left: 2px; margin-right: 3px; }
  .services li:nth-child(3) { width: 100%; }

  .signature { position: absolute; left: 0; width: 100%; top: 330px; text-align: center; color: var(--cream); }
  .signature__name { font-family: "Great Vibes", cursive; font-size: 36px; line-height: 1; text-shadow: 0 1px 2px rgba(0,0,0,0.25); }
  .signature__role { font-family: "Quicksand", sans-serif; font-size: 16px; letter-spacing: 1px; }
</style>
</head>
<body>
<main class="canvas">
  <section class="card card--front">
    <div class="logo-mark logo-mark--small" role="img" aria-label="Brand mark circle">
      <span class="logo-mark__name">Sláine<br>Dunleavy</span>
    </div>
    <div class="holder">
      <h1 class="holder__name">Sláine Dunleavy</h1>
      <p class="holder__role">Massage Therapist</p>
    </div>
    <ul class="contact">
      <li><svg viewBox="0 0 10 10"><path d="M2 0.5 L3.6 2.6 L2.7 3.6 Q4 6 6.4 7.3 L7.4 6.4 L9.5 8 L8.3 9.5 Q3 8.6 0.5 1.7 Z" fill="#a8731f"/></svg>(+353) 87 216 4093</li>
      <li><svg viewBox="0 0 10 10"><rect x="0.5" y="2" width="9" height="6.5" fill="#c9a14a"/><path d="M0.5 2 L5 5.6 L9.5 2" fill="none" stroke="#fff" stroke-width="0.8"/></svg>regenerate@slainedunleavy-example.com</li>
      <li><svg viewBox="0 0 10 10"><circle cx="5" cy="5" r="4.3" fill="none" stroke="#a8731f" stroke-width="1"/><ellipse cx="5" cy="5" rx="1.9" ry="4.3" fill="none" stroke="#a8731f" stroke-width="0.8"/><path d="M0.7 5 H9.3" stroke="#a8731f" stroke-width="0.8"/></svg>www.slainedunlevy-example.com</li>
    </ul>
    <ul class="services">
      <li>Swedish</li>
      <li>Deep Tissue</li>
      <li>Advanced Therapeutic</li>
    </ul>
  </section>

  <section class="card card--back">
    <div class="logo-mark logo-mark--large" role="img" aria-label="Brand mark circle"></div>
    <div class="signature">
      <p class="signature__name">Sláine Dunleavy</p>
      <p class="signature__role">massage therapist</p>
    </div>
  </section>
</main>
</body>
</html>
```